Accommodation in an Executive Apartment for rent could be a Bed and breakfast,

Currently have a website and like the overall look but it needs revamping and want to add an instant booking button, which I would do later as the unit has a channel manager. Also want to be able to post blogs, etc. Need it to be viewed well on smart phones/tablets. all information related to this unit is on the current site which is www.hollowmerestays.com.au if you would view websites similar to roomvela.com and travonix.com Must be able to be coded in Wordpress

The current design is done in Wordpress so would want this functionality in any new design.

Target Market(s)

Workers at Parliamentary triangle, Canberra. Workers at Marlow centre Deakin, Workers at Westbrook Ellis Hanley Hospital, Workers at Fernvale Hospital, Public Servants Woden, Workers in Deakin ACT

Industry/Entity Type

Accommodation

Number of Pages Required

5+ page

Font styles to use
Sans Serif

Colors
ec1f27

Requirements
Must have
• Must have a classy look about it. Less clicks through the better. Not to wordy. Hard hitting points,
Nice to have
• Would like to retain the same colour theme and look
Should not have
• anything tacky

```html
<!DOCTYPE html>
<html lang="en">
<head>
<meta charset="utf-8">
<title>Hollowmere Stays Bed and Breakfast</title>
<link rel="stylesheet" href="https://fonts.googleapis.com/css2?family=Ubuntu:wght@400;500&family=Arimo:wght@400;700&family=Courgette&display=swap">
<style>
  :root {
    --brand-red: #d9371f;
    --brand-red-dark: #b8231a;
    --brand-red-light: #e7502c;
    --nav-cream: #efe6cc;
    --nav-cream-dark: #e2d6b4;
    --page-bg: #faf9f5;
    --ink: #1b1b1b;
    --nav-ink: #3a3a3a;
    --panel-bg: rgba(38, 34, 32, 0.84);
    --field-bg: #ecebea;
    --footer-bg: #222222;
    --footer-ink: #e4e4e4;
    --white: #ffffff;
  }
  * { box-sizing: border-box; margin: 0; padding: 0; }
  html, body { width: 1085px; height: 1200px; overflow: hidden; }
  body { position: relative; background: var(--page-bg); font-family: "Arimo", Arial, sans-serif; color: var(--ink); }

  .site-header {
    position: absolute; left: 0; top: 0; width: 1085px; height: 127px;
    background: radial-gradient(ellipse at 50% 60%, var(--brand-red-light), var(--brand-red-dark) 85%);
    display: flex; align-items: center; justify-content: center;
  }
  .brand-name {
    font-family: "Ubuntu", sans-serif; font-weight: 400; color: var(--white);
    font-size: 28px; letter-spacing: 1px;
  }

  .main-nav {
    position: absolute; left: 0; top: 127px; width: 1085px; height: 52px;
    background: linear-gradient(var(--nav-cream), var(--nav-cream-dark));
    border-bottom: 1px solid #cdbf99;
  }
  .main-nav a {
    position: absolute; top: 17px; font-family: "Ubuntu", sans-serif; font-size: 15px;
    letter-spacing: 1.4px; color: var(--nav-ink); text-decoration: none;
  }
  .main-nav a.is-active { color: var(--brand-red); }

  .hero {
    position: absolute; left: 0; top: 179px; width: 1085px; height: 489px;
    border-bottom: 2px solid #d8d2c4;
  }
  .hero-photo {
    position: absolute; inset: 0;
    background: linear-gradient(100deg, #8a6f52 0%, #c9a97e 30%, #e8d6b5 55%, #f3ebdb 75%, #d6c3a4 100%);
  }
  .hero-arrow { position: absolute; top: 182px; }
  .hero-arrow.prev { left: 12px; }
  .hero-arrow.next { right: 12px; }
  .hero-dots { position: absolute; left: 493px; top: 459px; display: flex; gap: 13px; }
  .hero-dots span { width: 7px; height: 7px; border-radius: 50%; background: rgba(255,255,255,0.85); }
  .hero-dots span.is-current { background: #333; }

  .booking-panel {
    position: absolute; left: 69px; top: 2px; width: 311px; height: 444px;
    background: var(--panel-bg); padding: 42px 0 0 38px;
  }
  .booking-title { font-family: "Courgette", cursive; color: var(--brand-red); font-size: 27px; font-weight: 400; margin-bottom: 24px; line-height: 1.2; }
  .field-label { display: block; color: var(--white); font-size: 12.5px; margin-bottom: 8px; }
  .field { background: var(--field-bg); border-radius: 4px; height: 47px; box-shadow: inset 0 2px 4px rgba(0,0,0,0.15); }
  .field.wide { width: 234px; margin-bottom: 24px; }
  .field-row { display: flex; gap: 18px; }
  .field-row .field-group:first-child .field { width: 64px; }
  .field-row .field-group:nth-child(2) .field { width: 71px; }
  .field-row .field-group:last-child .field { width: 64px; }
  .field-row .field-group:nth-child(2) { margin-left: -2px; }
  .booking-button {
    margin-top: 33px; width: 234px; height: 47px; border-radius: 4px;
    background: linear-gradient(#ffffff, #dcdcdc); border: 1px solid var(--brand-red-dark);
    color: var(--brand-red-dark); font-family: "Ubuntu", sans-serif; font-weight: 500;
    font-size: 17px; letter-spacing: 2px; display: flex; align-items: center; justify-content: center;
  }

  .find-us-badge {
    position: absolute; left: 73px; top: 721px; width: 150px; height: 42px; border-radius: 21px;
    background: var(--brand-red); color: var(--white); font-family: "Ubuntu", sans-serif;
    font-weight: 500; font-size: 17.5px; letter-spacing: 1.5px;
    display: flex; align-items: center; justify-content: center;
  }
  .contact-details { position: absolute; left: 75px; top: 802px; width: 290px; font-size: 18.5px; }
  .contact-title { font-weight: 700; line-height: 32.5px; margin-bottom: 26px; }
  .contact-details p { line-height: 32.5px; }
  .contact-address { margin-bottom: 32px; }
  .contact-people { line-height: 29px !important; }

  .map-frame {
    position: absolute; left: 401px; top: 726px; width: 624px; height: 392px;
    border: 1px solid #333; background: var(--white); padding: 11px;
  }
  .map-area {
    position: relative; width: 601px; height: 367px;
    background: linear-gradient(135deg, #e8e4da 0%, #dfe8cf 40%, #e9e6dd 60%, #d6e6c0 100%);
  }
  .map-popup {
    position: absolute; left: 96px; top: 56px; width: 454px; height: 158px;
    background: var(--white); box-shadow: 0 1px 4px rgba(0,0,0,0.35); padding: 18px 18px;
  }
  .map-popup::after {
    content: ""; position: absolute; left: 204px; bottom: -16px;
    border-left: 16px solid transparent; border-right: 16px solid transparent; border-top: 16px solid var(--white);
  }
  .popup-name { color: #888; font-size: 16.5px; text-decoration: underline; }
  .popup-address { font-weight: 700; font-size: 16px; margin-top: 6px; }
  .popup-close { position: absolute; right: 14px; top: 14px; }

  .site-footer {
    position: absolute; left: 0; top: 1161px; width: 1085px; height: 39px;
    background: var(--footer-bg); color: var(--footer-ink); font-size: 15px;
  }
  .site-footer span { position: absolute; top: 11px; }
</style>
</head>
<body>
  <header class="site-header">
    <div class="brand-name">Hollowmere Stays</div>
  </header>

  <nav class="main-nav">
    <a class="is-active" href="#" style="left:106px">HOME</a>
    <a href="#" style="left:288px">FACILITY</a>
    <a href="#" style="left:509px">NEARBY</a>
    <a href="#" style="left:722px">GALLERY</a>
    <a href="#" style="left:902px">CONTACT</a>
  </nav>

  <section class="hero">
    <div class="hero-photo" role="img" aria-label="Photo of the apartment living room with armchairs, coffee table and dining set"></div>
    <svg class="hero-arrow prev" width="30" height="60" viewBox="0 0 30 60"><polyline points="28,2 2,30 28,58" fill="none" stroke="#fff" stroke-width="2"/></svg>
    <svg class="hero-arrow next" width="30" height="60" viewBox="0 0 30 60"><polyline points="2,2 28,30 2,58" fill="none" stroke="#fff" stroke-width="2"/></svg>
    <div class="hero-dots"><span class="is-current"></span><span></span><span></span><span></span></div>

    <form class="booking-panel">
      <h2 class="booking-title">Stay with us!</h2>
      <label class="field-label">CHECK IN</label>
      <div class="field wide"></div>
      <label class="field-label">CHECK OUT</label>
      <div class="field wide"></div>
      <div class="field-row">
        <div class="field-group"><label class="field-label">ADULTS</label><div class="field"></div></div>
        <div class="field-group"><label class="field-label">CHILDREN</label><div class="field"></div></div>
        <div class="field-group"><label class="field-label">NIGHTS</label><div class="field"></div></div>
      </div>
      <div class="booking-button">BOOKING</div>
    </form>
  </section>

  <div class="find-us-badge">FIND US!</div>

  <section class="contact-details">
    <h3 class="contact-title">Hollowmere Stays Bed and breakfast accommodation</h3>
    <p class="contact-address">14 Larkspur Crescent<br>Fernleigh Vale<br>ACT 2915<br>Australia</p>
    <p class="contact-people">Peter and Maree Holt<br>+61 400 555 218</p>
  </section>

  <div class="map-frame">
    <div class="map-area" role="img" aria-label="Street map showing the accommodation location">
      <div class="map-popup">
        <div class="popup-name">HOLLOWMERE STAYS BED AND BREAKFAST</div>
        <div class="popup-address">14 Larkspur Crescent, Fernleigh Vale ACT 2915, Australia</div>
        <svg class="popup-close" width="13" height="13" viewBox="0 0 13 13"><path d="M1 1L12 12M12 1L1 12" stroke="#888" stroke-width="2"/></svg>
      </div>
    </div>
  </div>

  <footer class="site-footer">
    <span style="left:75px">Copyright © 2015</span>
    <span style="left:231px">Hollowmere Stays Bed and Breakfast | Entries (RSS) and Comments (RSS)</span>
    <span style="left:882px">powered by</span>
  </footer>
</body>
</html>
```